WEBSITE REDESIGN FOR HAMMOCK MANUFACTURING COMPANY

VERITH HAMMOCKS - Verith Hammocks have been a specialist in hammock manufacturing business for over 20 years. FYI, the current website is WWW.SWAYNEST-EXAMPLE.COM.CN. We also have had a new logo designed . I have attached our new logo and old designs. You can use the old logo or new logo , so you can get a feel which one looks better with your design.

Target Market(s)

EUROPE AND NORTH AMERICA

Industry/Entity Type

Home And Garden

Font styles to use
Serif
Decorative
Script

Colors

Designer to choose colors to be used in the design.

Requirements
Must have
• Mobile friendly.
• Wildly creative and different. A website that we would expect to see 5 years from now.
• Pictures of hammocks and or people on hammock. Palm tree landscapes.
Nice to have
• Anything you feel would sell the garden hammock relaxation experience.

```html
<!DOCTYPE html>
<html lang="en">
<head>
<meta charset="utf-8">
<title>Verith Hammocks</title>
<link href="https://fonts.googleapis.com/css2?family=Lato:wght@400;700&display=swap" rel="stylesheet">
<style>
:root{
  --deep-green:#105b45;
  --lime:#7aba2a;
  --ink:#222;
  --muted:#444;
  --rule:#d9d9d9;
  --white:#fff;
}
*{margin:0;padding:0;box-sizing:border-box}
html,body{width:1200px;height:2222px;overflow:hidden;background:var(--white)}
body{font-family:'Lato',sans-serif;color:var(--ink);position:relative}
.abs{position:absolute}
.offer-bar{top:0;left:0;width:1200px;height:51px;background:var(--deep-green);color:var(--white);font-size:15px;line-height:51px;padding-left:75px}
.utility-bar{top:51px;left:0;width:1200px;height:50px;background:var(--lime);display:flex;justify-content:flex-end;align-items:center;gap:30px;padding-right:72px}
.utility-bar a{color:var(--white);text-decoration:none;font-size:13.5px;text-transform:uppercase}
.brand{top:122px;left:0;width:1200px;text-align:center;font-size:28px;font-weight:700;color:var(--deep-green);letter-spacing:0.5px}
.brand .dot{display:inline-block;width:14px;height:14px;border-radius:50%;background:var(--lime);margin-right:10px;vertical-align:middle}
.main-nav{top:196px;left:0;width:1200px;display:flex;justify-content:center;gap:48px}
.main-nav a{color:var(--ink);text-decoration:none;font-size:14px;font-weight:700;text-transform:uppercase}
.hero{top:237px;left:0;width:1200px;height:501px;background:linear-gradient(120deg,#6f8a5a 0%,#b9a58a 35%,#58b8c8 60%,#7aa8a8 80%,#4c6d43 100%)}
.hero-card{top:390px;left:615px;width:511px;height:195px;background:rgba(0,0,0,.78);text-align:center;color:var(--white)}
.hero-card h1{font-size:45px;font-weight:700;margin-top:16px}
.hero-card p{font-size:22px;margin-top:6px}
.btn{display:inline-block;background:var(--lime);color:var(--white);font-weight:700;font-size:19px;width:161px;height:44px;line-height:44px;margin-top:14px;text-transform:uppercase}
.section-title{left:75px;width:1051px;text-align:center;font-size:24px;font-weight:700;text-transform:uppercase;padding-bottom:22px;border-bottom:1px solid var(--rule)}
.product{width:240px;text-align:center}
.product .photo{height:249px}
.stars{color:var(--lime);font-size:18px;letter-spacing:2px;margin-top:22px;line-height:20px}
.product h3{font-size:18px;font-weight:400;text-transform:uppercase;margin-top:4px}
.price{color:var(--deep-green);font-weight:700;font-size:15px;margin-top:4px}
.post{width:330px;text-align:center}
.post .photo{height:261px}
.post h3{font-size:18px;font-weight:400;text-transform:uppercase;margin-top:20px}
.post .date{color:var(--deep-green);font-weight:700;font-size:15px;margin-top:4px}
.footer-rule{top:1847px;left:75px;width:1051px;border-top:1px solid var(--rule)}
.footer-col{top:1888px}
.footer-col h4{color:var(--deep-green);font-size:16px;font-weight:700;text-transform:uppercase;margin-bottom:8px}
.footer-col p,.footer-col li{font-size:15px;line-height:28px;color:var(--muted);list-style:none}
.phone{display:flex;align-items:center;gap:18px;margin-top:6px}
.social{display:flex;gap:14px;margin-top:10px}
.social span{width:22px;height:22px;border-radius:50%;background:#555}
.signup{display:flex;margin-top:10px}
.signup .field{width:270px;height:40px;border:1px solid #ccc;font-size:15px;line-height:38px;padding-left:14px;color:var(--ink)}
.signup .go{width:62px;height:40px;background:var(--lime);display:flex;align-items:center;justify-content:center}
.copyright{top:2166px;left:75px;font-size:13.5px;color:var(--muted)}
.cards{top:2163px;left:922px;display:flex;gap:11px}
.cards span{width:31px;height:20px;background:#9a9a9a;border-radius:2px}
</style>
</head>
<body>
<div class="abs offer-bar">Free shipping or some other offer goes here!</div>
<nav class="abs utility-bar"><a>CAD</a><a>Search</a><a>Gift Certificate</a><a>Account</a><a>0 Items in cart</a></nav>
<div class="abs brand"><span class="dot"></span>VERITH HAMMOCKS</div>
<nav class="abs main-nav"><a>Home</a><a>Products</a><a>About Us</a><a>News</a><a>FAQ</a><a>Contact</a><a>Personalize your hammock</a></nav>

<section class="abs hero" role="img" aria-label="Woman relaxing in a rope hammock under palm trees by the sea"></section>
<div class="abs hero-card">
  <h1>Verith Hammocks</h1>
  <p>Aenean tellus mauris, elementum sit amet.</p>
  <span class="btn">Shop now</span>
</div>

<h2 class="abs section-title" style="top:786px">Featured Products</h2>
<div class="abs product" style="top:881px;left:75px"><div class="photo" role="img" aria-label="Blue cushioned patio hanging lounger in a garden" style="background:linear-gradient(#3f5a2f,#2d4a22)"></div><div class="stars">★★★★★</div><h3>Patio Hanging</h3><div class="price">$120.00</div></div>
<div class="abs product" style="top:881px;left:345px"><div class="photo" role="img" aria-label="White rope hammock on a folding stand on grass" style="background:linear-gradient(#4d7a34,#2f5520)"></div><div class="stars">★★★★★</div><h3>Outdoor Folding</h3><div class="price">$120.00</div></div>
<div class="abs product" style="top:881px;left:615px"><div class="photo" role="img" aria-label="Striped camping hammock on a stand in a park" style="background:linear-gradient(#7a8a6a,#3f7a2a)"></div><div class="stars">★★★★★</div><h3>Outdoor Camping</h3><div class="price">$120.00</div></div>
<div class="abs product" style="top:881px;left:886px"><div class="photo" role="img" aria-label="Hanging hammock chair on a curved stand in a garden" style="background:linear-gradient(#5c8a3c,#3a6a28)"></div><div class="stars">★★★★★</div><h3>Hanging Hammock</h3><div class="price">$120.00</div></div>

<h2 class="abs section-title" style="top:1323px">Recent Blog Posts</h2>
<div class="abs post" style="top:1440px;left:75px"><div class="photo" role="img" aria-label="Colourful hammock under a palm on a white beach" style="background:linear-gradient(#3a8fd0,#9ad0e8 60%,#e9e4d8)"></div><h3>Curabitur pellentesque risus dui</h3><div class="date">SEP 21, 2018</div></div>
<div class="abs post" style="top:1440px;left:436px"><div class="photo" role="img" aria-label="Red hammock chair by the water" style="background:linear-gradient(#9aa6ae,#a8343a 60%,#8a6a55)"></div><h3>Curabitur pellentesque risus dui</h3><div class="date">SEP 21, 2018</div></div>
<div class="abs post" style="top:1440px;left:796px"><div class="photo" role="img" aria-label="Couple resting in a hammock between palms on a beach" style="background:linear-gradient(#4a8ac8,#a8cce0 60%,#d8c8a8)"></div><h3>Curabitur pellentesque risus dui</h3><div class="date">SEP 21, 2018</div></div>

<div class="abs footer-rule"></div>
<div class="abs footer-col" style="left:75px">
  <h4>Contact Us</h4>
  <p>21,Lindenweg Craft Park<br>Ostmoor Town, Harlow County,<br>Fenbridge,China</p>
  <div class="phone"><svg width="13" height="13" viewBox="0 0 24 24"><path fill="#444" d="M6.6 10.8a15 15 0 0 0 6.6 6.6l2.2-2.2a1 1 0 0 1 1-.25 11.4 11.4 0 0 0 3.6.57 1 1 0 0 1 1 1V20a1 1 0 0 1-1 1A17 17 0 0 1 3 4a1 1 0 0 1 1-1h3.5a1 1 0 0 1 1 1c0 1.25.2 2.45.57 3.57a1 1 0 0 1-.25 1z"/></svg><p>86-000-55501234</p></div>
</div>
<div class="abs footer-col" style="left:344px">
  <h4>Navigate</h4>
  <ul><li>Home</li><li>Products</li><li>About Us</li><li>News</li><li>Faq</li><li>Contact</li><li>Personalize Your</li></ul>
</div>
<div class="abs footer-col" style="left:541px">
  <h4>Follow us out there</h4>
  <div class="social"><span></span><span></span><span></span><span></span><span></span></div>
</div>
<div class="abs footer-col" style="left:794px">
  <h4>Join our mailing list</h4>
  <div class="signup"><div class="field">Enter Email Address</div><div class="go"><svg width="12" height="14" viewBox="0 0 12 14"><path d="M3 2l5 5-5 5" stroke="#fff" stroke-width="2.4" fill="none"/></svg></div></div>
</div>

<div class="abs copyright">Copyright © 2018 - Company Name &nbsp;All Right Reserved</div>
<div class="abs cards"><span></span><span></span><span></span><span></span><span></span></div>
</body>
</html>
```